Quirky Label Design for an Exciting UK-Based Organic Skincare Company!

We need label designs across our range of products, we are a high quality yet quirky organic skincare company called Simply Cordell, we use frosted glass packaging, and we are just wanting one design done for now, but the winning designer we would want to work with to design the rest of the labels for us. We also want them to design business cards and other literature at some point and maybe even a website page.

Our label design will go on a 63mm tall frosted glass jar which is 62mm in diameter. The actual label dimensions should be, 170 mm (W) x 50 mm (H). The idea is so that it wraps around the whole jar with the design at one side (at the front) and the ingredients on another (at the back).

LABEL 1
Organic Polynesian Whipped Body Butter
Vanilla Bean
120ml

Made with Organic Shea and Cocoa Butters and exotic Monoi de Tahiti

Ingredients (INCI): Organic Raw Shea Butter (Butyrospermum Parkii), Organic Raw Cocoa Butter (Theobroma Cacao), Monoi de Tahiti (Coconut (Cocos nucifera) oil (and) Tiare (Gardenia tahitensis) flower), Organic Sweet Almond Oil (Prunus Amygdalus Dulcis), Organic Madagascan Vanilla Extract (Vanillin)

Handmade by Simply Cordell Ltd
14 Fernwick Lane, Bournemouth BH4 9QT, UK
Batch:

OPTIONAL WRITING (if it fits in):
100% Natural and Organic
Intensely Moisturising

LABEL 2
Mango Smoothie
120ml

Ingredients (INCI): Organic Raw Shea Butter (Butyrospermum Parkii), Organic Raw Cocoa Butter (Theobroma Cacao), Monoi de Tahiti (Coconut (Cocos nucifera) oil (and) Tiare (Gardenia tahitensis) flower), Organic Sweet Almond Oil (Prunus Amygdalus Dulcis), Organic Mango Flavour (Aroma)

Batch:

100% Natural and Organic
Intensely Moisturising

I have attached a picture of the jar we use and the lid we use for these products, as well as our logo. I've also attached a 'Handmade in Dorset' stamp which we'd like to go on there if possible, along with a shelf life symbol.

I am thinking the background colour of the labels will be either white or even brown paper colour. Perhaps it would be interesting to see it in both. UPDATE: We have decided on white background now, not brown.

The final design should denote handmade, organic, high quality, pure, yet quirky and original / unique. I am thinking perhaps a seemingly hand-drawn black leaf outline? Could fit the bill, but as I say, up to you. Something that says handmade yet professional.

I'd like to have the original Photoshop files from the winning designer so we can use them as a template for the rest of our horizontal labels.
Updates

Project Deadline Extended
Reason: Just need a few more days for designs we like to be worked on further, and to review new designs!

Target Market(s)

Everyone that appreciates a good quality skincare product focusing on natural & organic. Price is mid-range to high

Industry/Entity Type

It Company

Requirements
Must have
• Must make the product look high quality & organic yet quirky and accessible. Must have our logo and the shelf life symbol and the writing as above.
Nice to have
• Nice to have the 'handmade' stamp attached, but not absolutely necessary if it doesn't fit within your design.

```html
<!DOCTYPE html>
<html lang="en">
<head>
<meta charset="utf-8">
<title>Simply Cordell — Whipped Body Butter Labels</title>
<link rel="stylesheet" href="https://fonts.googleapis.com/css2?family=Dosis:wght@500;600;700&family=Sriracha&display=swap">
<style>
  :root {
    --backdrop: #c9c9c9;
    --vanilla: #c2d12e;
    --vanilla-deep: #b3c226;
    --mango: #efb04f;
    --mango-deep: #c8802a;
    --ink: #222222;
    --script: #e7ec3c;
    --script-mango: #f2b24c;
    --paper: #ffffff;
    --band: #f1f1f1;
    --band-text: #2a2a2a;
    --ornament: rgba(30, 30, 30, 0.35);
  }
  * { box-sizing: border-box; margin: 0; padding: 0; }
  html, body { width: 1200px; height: 1121px; overflow: hidden; }
  body {
    background: var(--backdrop);
    font-family: "Dosis", sans-serif;
    position: relative;
  }
  .label {
    position: absolute;
    top: 496px;
    width: 272px;
    height: 252px;
    overflow: hidden;
  }
  .label--vanilla { left: 264px; }
  .label--mango { left: 660px; }

  .label__panel {
    position: absolute;
    inset: 0 0 40px 0;
  }
  .label--vanilla .label__panel {
    background: linear-gradient(90deg, var(--vanilla-deep), var(--vanilla) 30%, var(--vanilla) 70%, var(--vanilla-deep));
  }
  .label--mango .label__panel {
    background: linear-gradient(90deg, var(--mango-deep), var(--mango) 30%, var(--mango) 75%, #e9a644);
  }

  .label__sprig {
    position: absolute;
    top: 2px;
    width: 56px;
    height: 90px;
    border-radius: 28px;
    background: var(--ornament);
  }
  .label__sprig--left { left: 6px; }
  .label__sprig--right { right: 6px; }

  .label__brand {
    position: absolute;
    top: 24px;
    left: 66px;
    width: 140px;
    text-align: center;
    font-family: "Dosis", sans-serif;
    font-weight: 700;
    font-size: 25px;
    line-height: 27px;
    letter-spacing: 1px;
    text-transform: uppercase;
    color: var(--paper);
  }

  .label__title {
    position: absolute;
    top: 106px;
    left: 36px;
    width: 200px;
    height: 58px;
    background: var(--ink);
    border-radius: 4px;
    display: flex;
    flex-direction: column;
    justify-content: center;
    align-items: center;
    font-family: "Sriracha", cursive;
    font-size: 17px;
    line-height: 22px;
  }
  .label--vanilla .label__title { color: var(--script); }
  .label--mango .label__title { color: var(--script-mango); }

  .label__tag {
    position: absolute;
    top: 180px;
    height: 32px;
    background: var(--paper);
    color: var(--ink);
    display: flex;
    align-items: center;
    justify-content: center;
    text-align: center;
    font-weight: 600;
    border-radius: 2px;
  }
  .label__flavour {
    left: 22px;
    width: 40px;
    font-size: 11px;
    line-height: 12px;
  }
  .label__volume {
    left: 212px;
    width: 40px;
    font-size: 15px;
  }

  .label__claims {
    position: absolute;
    top: 182px;
    left: 66px;
    width: 140px;
    text-align: center;
    font-weight: 600;
    font-size: 10.5px;
    line-height: 14px;
  }
  .label--vanilla .label__claims { color: var(--ink); }
  .label--mango .label__claims { color: var(--paper); }

  .label__band {
    position: absolute;
    left: 0;
    right: 0;
    bottom: 0;
    height: 40px;
    background: linear-gradient(180deg, var(--paper) 0 26px, var(--band) 26px);
    white-space: nowrap;
    overflow: hidden;
  }
  .label__band-text {
    position: absolute;
    top: 4px;
    left: -4px;
    font-weight: 700;
    font-size: 11.5px;
    letter-spacing: 1.4px;
    color: var(--band-text);
    text-transform: uppercase;
    word-spacing: 1px;
  }
</style>
</head>
<body>

  <section class="label label--vanilla" aria-label="Vanilla Bean body butter label">
    <div class="label__panel"></div>
    <div class="label__sprig label__sprig--left" role="img" aria-label="Hand-drawn leaf sprig and flower outline"></div>
    <div class="label__sprig label__sprig--right" role="img" aria-label="Hand-drawn leaf sprig and flower outline"></div>
    <div class="label__brand">Simply<br>Cordell</div>
    <div class="label__title"><span>Organic Polynesian</span><span>Whipped Body Butter</span></div>
    <div class="label__tag label__flavour">Vanilla<br>Bean</div>
    <p class="label__claims">100% Natural And Organic<br>Intensely Moisturising</p>
    <div class="label__tag label__volume">120ml</div>
    <div class="label__band"><span class="label__band-text">Monoi de Tahiti &nbsp; Made with organic shea and co</span></div>
  </section>

  <section class="label label--mango" aria-label="Mango Smoothie body butter label">
    <div class="label__panel"></div>
    <div class="label__sprig label__sprig--left" role="img" aria-label="Hand-drawn leaf sprig and flower outline"></div>
    <div class="label__sprig label__sprig--right" role="img" aria-label="Hand-drawn leaf sprig and flower outline"></div>
    <div class="label__brand">Simply<br>Cordell</div>
    <div class="label__title"><span>Organic Polynesian</span><span>Whipped Body Butter</span></div>
    <div class="label__tag label__flavour">Mango<br>Smoothie</div>
    <p class="label__claims">100% Natural And Organic<br>Intensely Moisturising</p>
    <div class="label__tag label__volume">120ml</div>
    <div class="label__band"><span class="label__band-text">Monoi de Tahiti &nbsp; Made with organic shea and co</span></div>
  </section>

</body>
</html>
```